Vensol Holdings Web Design

Vensol Holdings Limited Shenzhen

This project is a 10 page launch website.
Our client is seeking a contemporary homepage design for a Holdings company. Once we are happy with the homepage design and select designer we will request a secondary page design.

Please see attached company LOGO for an idea of style, it incorporates the traditional Chinese furniture lattice work. The Corvel crest website is one of our clients favorite so we would like to see a similar homepage design to this website.

Use the websites below for reference purpose. The first two are Chinese and the second two are international. We would like to see elements of both but more focus on international design.

http://www.evergrande.com/http://www.taurenfield.com/pub/default.aspx http://www.corvelcrest.com/zh/maldives_lorinhaven/
http://www.quelba-studio.com
http://media-cache-ex0.snapvalu.com/originals/71/a3/19/71a319c5b2d04e8f6a17c3b9e5d0f4a1.jpg

Company Background
VENSOL HOLDINGS, located in Qianhai, China, is a new real-estate project operator, structuring urban-rural real-estate investment and development, and industrial fund investment. The company also invests in supply chain management and supporting infrastructures. To create new spaces and livable cities Vensol Holdings develop win-win strategic partnerships with a number of institutions. Currently cooperating with Tianjing North Lumore, China urban and rural integrated demonstration.

Target Market(s)

B2B property investment. Target market customers are senior level management/decision makers of large corporations. Focusing geographically on the domestic market first and expanding internationally in 2nd and 3rd years.

Industry/Entity Type

Investment

Requirements
Must have
• Since this is a new company, we would like to the website representing growth and power, E.g. like a growing tree.
Should not have
• Low-level vectors such as curency symbols, American dollar.

```html
<!DOCTYPE html>
<html lang="en">
<head>
<meta charset="utf-8">
<title>Vensol Holdings</title>
<link rel="stylesheet" href="https://fonts.googleapis.com/css2?family=Open+Sans:wght@400;600&family=Ropa+Sans&family=PT+Serif&display=swap">
<style>
:root{
  --gold:#b38c38;
  --gold-dark:#8a6a1e;
  --gold-light:#cdae62;
  --cream:#fbf3e4;
  --text-gray:#8a8a8a;
  --heading-gray:#555;
  --line:#dcdcdc;
  --white:#fff;
}
*{margin:0;padding:0;box-sizing:border-box}
html,body{width:972px;height:1200px;overflow:hidden;background:var(--white)}
body{position:relative;font-family:"Open Sans",sans-serif;color:#555}
.abs{position:absolute}

.hero{left:0;top:0;width:972px;height:525px;
  background:linear-gradient(180deg,#bfd8ee 0%,#dfe9ee 30%,#b9c9b5 50%,#5f8f45 68%,#3f7330 85%,#2f5e25 100%);
  box-shadow:0 6px 10px rgba(0,0,0,.12)}
.nav-band{left:0;top:65px;width:972px;height:50px;
  background:linear-gradient(180deg,#c9a551 0%,#b08632 100%)}
.nav{left:0;top:81px;height:20px}
.nav a{position:absolute;color:var(--white);text-decoration:none;font-size:13.5px;white-space:nowrap}
.nav .active::after{content:"";position:absolute;left:-5px;right:-5px;top:29px;height:3px;background:#f1dca6}

.logo-panel{left:57px;top:33px;width:315px;height:108px;
  background:linear-gradient(180deg,#fff,#f1f1f1);
  clip-path:polygon(0 0,94% 0,100% 100%,0 100%);
  box-shadow:0 2px 6px rgba(0,0,0,.2)}
.logo-mark{left:75px;top:47px;width:78px;height:78px;border-radius:50%;border:2px solid var(--gold)}
.logo-name{left:161px;top:73px;font-size:20px;color:var(--gold);letter-spacing:.5px;white-space:nowrap}

.hero-title{left:0;width:972px;text-align:center;font-family:"PT Serif",serif;color:var(--white);
  text-shadow:0 1px 3px rgba(0,0,0,.4);white-space:nowrap}
.hero-title.small{top:304px;font-size:26px}
.hero-title.big{top:334px;font-size:34px}
.dots{left:451px;top:501px;display:flex;gap:3px}
.dots span{width:13px;height:13px;border-radius:50%;background:rgba(255,255,255,.45)}
.dots span:first-child{background:var(--white)}

.video-card{left:57px;top:573px;width:295px;height:218px;border:1px solid #e6e6e6;box-shadow:0 1px 4px rgba(0,0,0,.08)}
.section-title{font-family:"Ropa Sans",sans-serif;font-size:20px;color:var(--heading-gray);white-space:nowrap}
.video-thumb{left:74px;top:621px;width:262px;height:160px;border-radius:5px;
  background:linear-gradient(160deg,#9fd1ea 0%,#5fa6cf 50%,#2f5f86 100%)}

.services-title{left:394px;top:576px;color:var(--gold)}
.services{left:394px;top:607px;width:221px;list-style:none}
.services li{height:25px;border-bottom:1px solid var(--line);font-size:11px;color:var(--gold);
  line-height:24px;padding-left:13px;position:relative;white-space:nowrap}
.services li:last-child{border-bottom:none}
.services li::before{content:"";position:absolute;left:2px;top:7px;border-left:5px solid var(--gold-dark);
  border-top:5px solid transparent;border-bottom:5px solid transparent}

.projects-title{left:647px;top:576px}
.project-thumb{left:648px;width:102px;height:77px}
.project-name{left:760px;font-size:13.5px;color:var(--heading-gray);white-space:nowrap}
.project-text{left:761px;width:160px;font-size:9.4px;line-height:15px;color:var(--text-gray)}

.footer{left:0;top:847px;width:972px;height:299px;
  background:linear-gradient(180deg,#c9a95a 0%,#b8923f 50%,#a07c2a 100%)}
.footer-title{font-size:16.5px;color:var(--white);white-space:nowrap}
.footer-text{font-size:9.9px;line-height:15px;color:var(--white)}
.news-date{font-size:11.5px;color:#5e4710;white-space:nowrap}
.news-text{font-size:9.9px;line-height:15px;color:var(--white)}
.field{left:666px;width:223px;background:linear-gradient(180deg,#fff,#f2f2f2);border:1px solid #d9c79a;
  font-size:9.8px;color:#666;padding:7px 10px}
.submit{left:825px;top:1050px;width:66px;height:22px;background:#5a430f;border:1px solid #3d2d08;border-radius:2px;
  color:var(--white);font-size:9.5px;font-weight:600;text-align:center;line-height:20px}

.bottom-bar{left:0;top:1146px;width:972px;height:54px;background:var(--cream)}
.copyright{left:71px;top:1166px;font-size:9.9px;color:#5e4710;white-space:nowrap}
.social{top:1158px;width:26px;height:26px;border-radius:50%;background:var(--gold-dark)}
</style>
</head>
<body>
<div class="abs hero" role="img" aria-label="Residential towers among landscaped parkland and a river at sunrise"></div>
<div class="abs nav-band"></div>
<nav class="abs nav">
  <a class="active" style="left:401px">HOME</a>
  <a style="left:474px">ABOUT US</a>
  <a style="left:575px">SERVICES</a>
  <a style="left:669px">PARTNERS</a>
  <a style="left:770px">NEWS</a>
  <a style="left:841px">CONTACT</a>
</nav>
<div class="abs logo-panel"></div>
<div class="abs logo-mark"></div>
<div class="abs logo-name">VENSOL HOLDINGS</div>

<div class="abs hero-title small">DUIS TINCIDUNT LECTUS QUIS DUI</div>
<div class="abs hero-title big">MORBI MAGNA TINCIDUNT MATTIS</div>
<div class="abs dots"><span></span><span></span><span></span><span></span></div>

<div class="abs video-card"></div>
<div class="abs section-title" style="left:75px;top:588px">Watch Our Latest Video</div>
<div class="abs video-thumb" role="img" aria-label="Glass office tower under construction against a blue sky"></div>
<svg class="abs" style="left:186px;top:682px" width="38" height="38" viewBox="0 0 38 38">
  <circle cx="19" cy="19" r="17" fill="#fff" stroke="#222" stroke-width="3"/>
  <path d="M15 12 L26 19 L15 26 Z" fill="#222"/>
</svg>

<div class="abs section-title services-title">Services We Provide</div>
<ul class="abs services">
  <li>Suspendisse vulputate aliquam dui.</li>
  <li>Nulla elementum dui ut augue.</li>
  <li>Aliquam vehicula mi at mauris.</li>
  <li>Maecenas placerat nisl at consequat</li>
  <li>Phasellus felis dolor scelerisque tempus</li>
  <li>Vestibulum ligula augue bibendum</li>
  <li>Aliquam vehicula mauris.</li>
</ul>

<div class="abs section-title projects-title">Recent Projects</div>
<div class="abs project-thumb" style="top:610px;background:linear-gradient(135deg,#6b5a48,#c9c2b8 55%,#3a302a)" role="img" aria-label="House for sale sign in front of a brick building"></div>
<div class="abs project-name" style="top:607px">Duis tincidunt</div>
<div class="abs project-text" style="top:627px">Suspendisse vulputate aliquam dui. Nulla elementum dui ut augue. Aliquam vehicula mi at mauris. Maecenas placerat, nisl at</div>
<div class="abs project-thumb" style="top:703px;background:linear-gradient(135deg,#d9c8b6,#b0845e 50%,#c94b4b)" role="img" aria-label="Family reviewing documents together at home"></div>
<div class="abs project-name" style="top:698px">Bandit sed nulla</div>
<div class="abs project-text" style="top:718px">Suspendisse vulputate .aliquam dui. Nulla elementum dui ut augue. Aliquam vehicula mi at mauris. Maecenas nisl at conse</div>

<div class="abs footer"></div>
<div class="abs footer-title" style="left:65px;top:880px">ABOUT OUR COMPANY</div>
<p class="abs footer-text" style="left:65px;top:909px;width:265px">Donec scelerisque leo ac risus. Praesent sit amet est. In dictum, dolor eu dictum porttitor, enim felis viverra mi, eget luctus massa purus quis odio. Etiam nulla massa, pharetra facilisis, volutpat in, imperdiet sit amet, sem. Aliquam nec erat at purus cursus interdum.</p>
<p class="abs footer-text" style="left:65px;top:993px;width:265px">Vestibulum ligula augue, bibendum accumsan, vestibulum ut, commodo a, mi. Morbi ornare gravida elit. Integer congue, augue et malesuada iaculis, ipsum dui aliquet felis, at cursus magna nisl nec elit.</p>

<div class="abs footer-title" style="left:381px;top:880px">LATEST NEWS &amp; BLOG</div>
<div class="abs news-date" style="left:381px;top:910px">20 December 2013</div>
<p class="abs news-text" style="left:381px;top:926px;width:260px">Praesent sit amet est. In dictum, dolor eu dictum porttitorEnim felis viverra mi eget luctus</p>
<div class="abs news-date" style="left:381px;top:970px">18 December 2013</div>
<p class="abs news-text" style="left:381px;top:986px;width:260px">Donec scelerisque leo ac risus. Praesent sit amet est. In dictum, dolor eu dictum porttitor</p>
<div class="abs news-date" style="left:381px;top:1030px">18 December 2013</div>
<p class="abs news-text" style="left:382px;top:1047px;width:260px">Llibero, a tempus libero lectus feugiat felis</p>

<div class="abs footer-title" style="left:664px;top:880px">ENQURIY FORM</div>
<div class="abs field" style="top:915px;height:25px">Your Name</div>
<div class="abs field" style="top:947px;height:25px">Email address</div>
<div class="abs field" style="top:980px;height:63px">Message/Comment</div>
<div class="abs submit">SUBMIT</div>

<div class="abs bottom-bar"></div>
<div class="abs copyright">© 2014 Company Name. All right reserved. Term of Use</div>
<div class="abs social" style="left:783px"></div>
<div class="abs social" style="left:813px"></div>
<div class="abs social" style="left:843px"></div>
<div class="abs social" style="left:873px"></div>
</body>
</html>
```